Lone Star Wetland Flora Stewardship Guild

We need to design the home page of this new website. We would like a fun website design for provides as a resource for members and information for potential members.
Please design so that we can see a portion of background on each side on the website.
I just need the final design files psd no coding needed.
Attached is their logo (colors are not 100% set in stone either so can mess with those as I did in the quick mockup attached)
Attached is a pdf newsletter they send out, you can get a feel for them and what they are about. The design is crappy and we are here to fix that going forward and we are starting with the website.
Here are some quick example websites (design style is open)
- I attached a quick mockup i did just for a content visual but by all means do what you want.
- http://www.brightpathleaders.example/
- http://www.civicunityhub.example/
- http://preview.webskinvault.example/show.php?cat=layouts&host=skinbazaar&temp=novaline
- http://www.meadowkeep.example/
- http://www.urbangleaners.example/
- http://www.projectcozyknit.example/
here are some of the other chapters website (pretty bad!)
and here are some of the others:
- http://www.dwrvcs.example/
- http://kwfg.example/
- http://www.blvcg.example/
Content Items that need to be included:
1. Logo
2. Menu - home, about, members, resources, events, membership, contact
3. Become a member - button or action
4. social links - chatterloop, workweave, clipstream
5. banner - that needs to explain their purpose "Promoting environmental stewardship through operations, research, education and outreach" (or this can be worked into the design)
6. Upcoming event (s)
7. Advertisement - members can place an ad on the website, this can be a placeholder for now
8. newsletter signup
9. advertise with us - this link can be in the footer
30-60 years of age, succesfull (household budgets of 120K+ men and women that live in texas.
Education

```html
<!DOCTYPE html>
<html lang="en">
<head>
<meta charset="utf-8">
<title>Lone Star Wetland Flora Stewardship Guild</title>
<link href="https://fonts.googleapis.com/css2?family=Raleway:wght@400;500;600;700&family=Open+Sans:ital,wght@0,400;0,600;1,400&family=Source+Sans+3:ital,wght@0,400;0,600;1,400&display=swap" rel="stylesheet">
<style>
:root{
  --navy:#0b2159;
  --crimson:#9e2445;
  --page:#f7f7f7;
  --text:#2b2b2b;
  --rule:#d8d8d8;
  --dark:#222;
}
*{margin:0;padding:0;box-sizing:border-box}
html,body{width:998px;height:1200px;overflow:hidden}
body{background:var(--page);font-family:"Open Sans",sans-serif;color:var(--text);position:relative}
a{color:inherit;text-decoration:none}

.topbar{position:absolute;top:0;left:0;width:998px;height:37px;background:var(--navy)}
.social{display:flex;gap:10px;position:absolute}
.social span{width:21px;height:21px;border-radius:50%;background:#fff;display:block}
.topbar .social{left:638px;top:7px}
.toplinks{position:absolute;left:758px;top:11px;display:flex;gap:22px;color:#fff;font-size:12px;font-family:"Source Sans 3",sans-serif}
.toplinks a{display:flex;align-items:center;gap:5px}

.masthead{position:absolute;top:37px;left:0;width:998px;height:110px;background:#fbfbfb}
.brand{position:absolute;left:95px;top:28px;display:flex;align-items:center;gap:10px}
.brand .dot{width:26px;height:26px;border-radius:50%;background:var(--crimson)}
.brand .mark{font-family:"Raleway",sans-serif;font-weight:700;font-size:44px;color:var(--navy);letter-spacing:1px}
.tagline{position:absolute;left:378px;top:20px;font-family:"Raleway",sans-serif;font-size:21px;line-height:33px;color:#111;letter-spacing:.5px;text-transform:uppercase}
.tagline span{display:block}
.tagline span+span{padding-left:40px}
.join{position:absolute;left:736px;top:32px;width:178px;height:38px;background:#111;border:2px solid #111;outline:1px solid #fff;outline-offset:-4px;color:#fff;font-family:"Raleway",sans-serif;font-size:16px;display:flex;align-items:center;justify-content:center;border-radius:4px;text-transform:uppercase}

.mainnav{position:absolute;top:147px;left:0;width:998px;height:41px;background:var(--crimson)}
.mainnav ul{list-style:none;display:flex;justify-content:space-between;width:790px;margin-left:105px;height:41px;align-items:center}
.mainnav a{color:#fff;font-family:"Source Sans 3",sans-serif;font-weight:600;font-size:14px;text-transform:uppercase;text-shadow:0 1px 1px rgba(0,0,0,.3)}

.hero{position:absolute;top:199px;left:83px;width:834px;height:351px;background:#fff;border:1px solid #e3e3e3;padding:2px}
.hero-photo{width:100%;height:100%;background:linear-gradient(180deg,#6f8f87 0%,#7fa393 30%,#5f8b6a 60%,#3d5a4e 100%);position:relative}
.hero-cap{position:absolute;left:0;right:0;bottom:0;height:78px;background:rgba(35,40,40,.78);color:#fff;font-family:"Raleway",sans-serif;font-weight:500;font-size:21px;line-height:28px;padding:12px 18px;letter-spacing:.3px}
.arrow{position:absolute;top:137px;width:22px;height:28px;background:rgba(230,230,230,.85);display:flex;align-items:center;justify-content:center}
.arrow.prev{left:0}.arrow.next{right:0}

h2{font-family:"Raleway",sans-serif;font-weight:500;font-size:27px;color:var(--crimson);letter-spacing:.5px}
.welcome{position:absolute;left:85px;top:574px;width:560px}
.welcome p{margin-top:10px;font-size:13.2px;line-height:18.3px;padding-left:2px}

.events{position:absolute;left:83px;top:745px;width:558px}
.event{display:flex;gap:12px;padding:0 3px}
.event-photo{width:129px;height:86px;flex:none}
.event h3{font-family:"Source Sans 3",sans-serif;font-weight:600;font-size:13.2px;color:var(--navy);margin-top:-2px}
.event time{display:block;font-family:"Source Sans 3",sans-serif;font-style:italic;color:var(--crimson);font-size:12.5px;margin-top:2px}
.event p{font-size:12.3px;line-height:16px;margin-top:3px;padding-left:1px}
.events .list{margin-top:21px}
.divider{height:1px;background:var(--rule);margin:21px 0}
.view-all{position:absolute;left:451px;top:290px;width:104px;height:27px;background:var(--dark);color:#fff;border-radius:3px;font-family:"Raleway",sans-serif;font-size:15px;display:flex;align-items:center;justify-content:center;letter-spacing:.5px}

.newsletter{position:absolute;left:672px;top:579px;width:243px;height:140px;background:var(--navy);border-radius:4px;text-align:center}
.newsletter h4{font-family:"Raleway",sans-serif;font-weight:500;color:#fff;font-size:21px;margin-top:14px;letter-spacing:.5px}
.newsletter .field{position:absolute;left:25px;top:52px;width:189px;height:27px;background:#fff;border:1px solid #ccc;font-family:Arial,sans-serif;font-size:12px;color:#555;text-align:left;padding:6px}
.newsletter .signup{position:absolute;left:126px;top:94px;width:89px;height:28px;background:var(--crimson);color:#fff;font-family:"Raleway",sans-serif;font-weight:600;font-size:15px;display:flex;align-items:center;justify-content:center}

.ad{position:absolute;left:673px;top:750px;width:242px;height:313px}
.ad-photo{height:246px;background:linear-gradient(180deg,#3d88b0 0%,#2a5f80 35%,#1e2228 60%,#20242a 100%)}
.ad-brand{height:67px;background:#e3e3e3;display:flex;align-items:center;justify-content:flex-end;padding-right:16px;gap:8px;font-family:"Raleway",sans-serif;font-weight:700;font-size:22px;color:#222}
.ad-brand .dot{width:12px;height:12px;border-radius:50%;background:#2a7fb0}

.footer{position:absolute;top:1107px;left:0;width:998px;height:93px;background:var(--navy);color:#fff;font-family:Arial,sans-serif}
.footer nav{position:absolute;left:96px;top:30px;font-size:12.5px;display:flex;gap:17px}
.footer .copy{position:absolute;left:96px;top:59px;font-size:12.5px}
.footer .advertise{position:absolute;left:780px;top:21px;font-size:14px;text-decoration:underline}
.footer .social{left:802px;top:47px}
</style>
</head>
<body>
<header>
  <div class="topbar">
    <div class="social">
      <span role="img" aria-label="chatterloop"></span>
      <span role="img" aria-label="workweave"></span>
      <span role="img" aria-label="clipstream"></span>
    </div>
    <div class="toplinks">
      <a href="#"><svg width="16" height="11" viewBox="0 0 16 11"><rect x=".5" y=".5" width="15" height="10" fill="none" stroke="#fff"/><path d="M.5 .5 8 6l7.5-5.5" fill="none" stroke="#fff"/></svg>CONTACT</a>
      <a href="#"><svg width="12" height="13" viewBox="0 0 12 13"><path d="M4 1h7v11H4" fill="none" stroke="#fff" stroke-width="1.4"/><path d="M0 6.5h7M5 4l2.5 2.5L5 9" fill="none" stroke="#fff" stroke-width="1.4"/></svg>LOGIN</a>
    </div>
  </div>
  <div class="masthead">
    <div class="brand"><span class="dot"></span><span class="mark">LSWFSG</span></div>
    <div class="tagline"><span>Lone Star Wetland Flora</span><span>Stewardship Guild.</span></div>
    <a class="join" href="#">Become a Member</a>
  </div>
  <nav class="mainnav">
    <ul>
      <li><a href="#">Home</a></li><li><a href="#">About</a></li><li><a href="#">Members</a></li><li><a href="#">Resources</a></li><li><a href="#">Events</a></li><li><a href="#">Membership</a></li><li><a href="#">Contact</a></li>
    </ul>
  </nav>
</header>

<section class="hero">
  <div class="hero-photo" role="img" aria-label="Water lily blooming among lily pads and reeds on a pond">
    <span class="arrow prev"><svg width="10" height="14"><path d="M7 2 2 7l5 5" fill="none" stroke="#fff" stroke-width="2.5"/></svg></span>
    <span class="arrow next"><svg width="10" height="14"><path d="M3 2l5 5-5 5" fill="none" stroke="#fff" stroke-width="2.5"/></svg></span>
    <div class="hero-cap">Promoting environmental stewardship through operations,research, education and outreach</div>
  </div>
</section>

<section class="welcome">
  <h2>Welcome to LSWFSG</h2>
  <p>The Lone Star Wetland Flora Stewardship Guild, Inc. is an organization of scientists, educators, students, commercial pesticide applicators, administrators, and concerned individuals interested in the management and study of aquatic plants. The membership reflects a diversity of federal, state, and local agencies; universities and colleges around the world; corporations; and small businesses.</p>
</section>

<section class="events">
  <h2 style="padding-left:2px">Upcoming Events</h2>
  <div class="list">
    <article class="event">
      <div class="event-photo" role="img" aria-label="Pond with lily pads under a blue sky" style="background:linear-gradient(180deg,#8fb8e0 0%,#a9c9e6 35%,#5e8a3e 55%,#6e7a55 100%)"></div>
      <div>
        <h3>2014 Northeast Pondweed Stewards Council Annual Conference</h3>
        <time>January 21, 2014 -January 23, 2014</time>
        <p>Lorem Ipsum is simply dummy text of the printing and typesetting industry. Lorem Ipsum has been the industry's standard dummy text ever since the 1500s,</p>
      </div>
    </article>
    <div class="divider"></div>
    <article class="event">
      <div class="event-photo" role="img" aria-label="Reeds and trees along a calm pond" style="background:linear-gradient(180deg,#d9e4ea 0%,#8fa86a 35%,#4f6f3a 65%,#6a7f5a 100%)"></div>
      <div>
        <h3>2014 Northeast Pondweed Stewards Council Annual Conference</h3>
        <time>January 21, 2014 -January 23, 2014</time>
        <p>Lorem Ipsum is simply dummy text of the printing and typesetting industry. Lorem Ipsum has been the industry's standard dummy text ever since the 1500s,</p>
      </div>
    </article>
  </div>
  <a class="view-all" href="#">Veiw All</a>
</section>

<aside class="newsletter">
  <h4>Newsletter Signup</h4>
  <div class="field">Email Address</div>
  <a class="signup" href="#">Sign Up</a>
</aside>

<aside class="ad">
  <div class="ad-photo" role="img" aria-label="PureFlow Max algaecide jug and bag over blue water"></div>
  <div class="ad-brand"><span class="dot"></span>Clearbrook Labs</div>
</aside>

<footer class="footer">
  <nav>
    <a href="#">Home</a><span>|</span><a href="#">About</a><span>|</span><a href="#">Members</a><span>|</span><a href="#">Resources</a><span>|</span><a href="#">Events</a><span>|</span><a href="#">Membership</a><span>|</span><a href="#">Contact</a>
  </nav>
  <div class="copy">Copyright © 2014 LSWFSG. All rights reserved.</div>
  <a class="advertise" href="#">advertise with us</a>
  <div class="social">
    <span role="img" aria-label="chatterloop"></span>
    <span role="img" aria-label="workweave"></span>
    <span role="img" aria-label="clipstream"></span>
  </div>
</footer>
</body>
</html>
```